Clear Plastic Card Design

I am looking to have a business card designed from my logo icon. I am looking to match the style of a different business card I have attached in the files.
Looking for a card that is plastic, with layers of transparency in the shape of my logo icon (also attached in the files) - not a circle like the other card. The winning design will incorporate the red icon logo on the front and back and include the charity's name, "Light for the Weary Souls" in the same or similar font, as well as an email and phone number. For now, use the email: email@lightfortheweary-mail.org and the phone number 555-382-7194.
We like how the sample business card has transparency, partial and full opacity layers and a matching color scheme. Files will need to be in vector so that our business card printing company can work with it.
UPDATE:
We've some excellent designs in, thank you everyone! I got an early review from the owner, and he requested a minor redirect to find his perfect design. He wants the design to stand out by NOT being a rectangle. Try instead a circle, square, or best yet - something that falls in the outline of the logo icon, either fully or partially. Thank you, everyone!
Light for the Weary Souls text should be incorporated as well as a phone and email.

```html
<!DOCTYPE html>
<html lang="en">
<head>
<meta charset="utf-8">
<title>Light for the Weary Souls – Business Card</title>
<link rel="stylesheet" href="https://fonts.googleapis.com/css2?family=Sora:wght@300;400&family=Poppins:wght@300;400;600&display=swap">
<style>
  :root {
    --backdrop: #f2f2f2;
    --card-top: #f2f0ec;
    --card-mid: #f1e4dc;
    --card-bottom: #efdcdc;
    --card-edge: #e0e0e0;
    --ink-grey: #707070;
    --accent-pink: #e07a93;
    --mark-peach: #f0a878;
    --mark-rose: #e3828a;
    --icon-red: #e06b73;
  }
  html, body {
    margin: 0;
    width: 1200px;
    height: 1200px;
    overflow: hidden;
    background: var(--backdrop);
  }
  .canvas { position: relative; width: 1200px; height: 1200px; }
  .card {
    position: absolute;
    left: 268px;
    width: 690px;
    height: 450px;
    overflow: visible;
    filter: drop-shadow(6px 8px 6px rgba(0,0,0,0.08));
  }
  .card--front { top: 112px; }
  .card--back { top: 653px; }
  .brand-line { font-family: "Sora", sans-serif; font-weight: 300; fill: var(--ink-grey); }
  .person-name { font-family: "Poppins", sans-serif; font-weight: 600; fill: var(--accent-pink); font-size: 29px; }
  .person-role { font-family: "Poppins", sans-serif; font-weight: 400; fill: var(--ink-grey); font-size: 24px; }
  .contact-text { font-family: "Poppins", sans-serif; font-weight: 300; fill: var(--ink-grey); font-size: 18px; letter-spacing: 0.3px; }
  .contact-ring { fill: none; stroke: var(--icon-red); stroke-width: 1; }
  .contact-glyph { fill: var(--icon-red); }
</style>
</head>
<body>
<div class="canvas">
  <svg width="0" height="0" style="position:absolute" aria-hidden="true">
    <defs>
      <linearGradient id="card-fill" x1="0" y1="0" x2="0" y2="1">
        <stop offset="0" stop-color="var(--card-top)"/>
        <stop offset="0.5" stop-color="var(--card-mid)"/>
        <stop offset="1" stop-color="var(--card-bottom)"/>
      </linearGradient>
      <linearGradient id="mark-fill" x1="0" y1="1" x2="1" y2="0">
        <stop offset="0" stop-color="var(--mark-rose)"/>
        <stop offset="1" stop-color="var(--mark-peach)"/>
      </linearGradient>
      <path id="card-outline" d="M80 0 H470 C580 0 674 90 674 218 C674 346 580 436 470 436 H80 A80 80 0 0 1 0 356 V80 A80 80 0 0 1 80 0 Z"/>
    </defs>
  </svg>

  <!-- Front -->
  <svg class="card card--front" viewBox="0 0 690 450">
    <use href="#card-outline" fill="url(#card-fill)" stroke="var(--card-edge)" stroke-width="1.5"/>
    <circle class="brand-dot" cx="100" cy="86" r="40" fill="url(#mark-fill)" opacity="0.9"/>
    <circle class="feature-disc" cx="555" cy="205" r="105" fill="url(#mark-fill)" opacity="0.85"/>
    <text class="brand-line" x="124" y="289" font-size="44">Light for the</text>
    <text class="brand-line" x="124" y="338" font-size="44">Weary Souls</text>
  </svg>

  <!-- Back -->
  <svg class="card card--back" viewBox="0 0 690 450">
    <use href="#card-outline" fill="url(#card-fill)" stroke="var(--card-edge)" stroke-width="1.5"/>
    <circle class="brand-dot" cx="186" cy="66" r="40" fill="url(#mark-fill)" opacity="0.9"/>
    <circle class="feature-disc" cx="500" cy="222" r="150" fill="url(#mark-fill)" opacity="0.85"/>
    <text class="brand-line" x="25" y="111" font-size="18">Light for the</text>
    <text class="brand-line" x="25" y="131" font-size="18">Weary Souls</text>

    <text class="person-name" x="26" y="211">Dana Whitlock</text>
    <text class="person-role" x="26" y="243">Marketing Director</text>

    <g class="contact contact--phone">
      <circle class="contact-ring" cx="38" cy="301" r="12.5"/>
      <path class="contact-glyph" d="M33 294.5 l3 -1 l2 4.5 l-2 1.5 a9 9 0 0 0 4.5 4.5 l1.5 -2 l4.5 2 l-1 3 c-7 1 -13 -5 -12.5 -12.5 z"/>
      <text class="contact-text" x="70" y="307">555-382-7194</text>
    </g>
    <g class="contact contact--email">
      <circle class="contact-ring" cx="38" cy="349" r="12.5"/>
      <rect class="contact-glyph" x="31" y="344" width="14" height="10" rx="1"/>
      <path d="M31.5 344.5 L38 350 L44.5 344.5" fill="none" stroke="#fff" stroke-width="1"/>
      <text class="contact-text" x="71" y="355">email@lightfortheweary-mail.org</text>
    </g>
  </svg>
</div>
</body>
</html>
```